High Tech Real Estate Startup needs a business card

We are developing an innovative real estate marketing product based around advanced search and virtual reality.

We talk to people, we need business cards.

Target Market(s)

The target market is technology professionals and realtors.

Contact Information for Business Card

The information to be included will include

Name
Title
Phone Number
E-mail Address
www.zelquin.com

It should use simple iconography for each one of those fields.

Font styles to use
Other font styles liked:
• Co, Jubilat, Avenir

Colors

Designer to choose colors to be used in the design.

Requirements
Must have
• Clean aesthetic,
• Good use of negative space.
• It should use our company logo, shown in the attached file. It is able to use the negative of that logo (coloured font and white background) and I have attached other acceptable accent colours in a swatch file.
Should not have
• Should not be too busy
• No extraneous text (slogans, tag lines etc)

```html
<!DOCTYPE html>
<html lang="en">
<head>
<meta charset="utf-8">
<title>Zelquin Business Card</title>
<link rel="stylesheet" href="https://fonts.googleapis.com/css2?family=Montserrat:wght@500&family=Open+Sans:wght@400;600&display=swap">
<style>
  :root {
    --backdrop: #3a3a3b;
    --card: #1f2021;
    --teal: #3fbdbf;
    --ink: #f2f2f2;
    --ink-soft: #c9c9c9;
  }
  * { margin: 0; padding: 0; box-sizing: border-box; }
  html, body { width: 799px; height: 1200px; overflow: hidden; }
  body {
    background: var(--backdrop);
    font-family: "Open Sans", Arial, sans-serif;
    position: relative;
  }
  .card {
    position: absolute;
    left: 80px;
    width: 640px;
    height: 366px;
    background: var(--card);
    border-radius: 28px;
    overflow: hidden;
  }
  .card--front { top: 117px; }
  .card--back { top: 717px; }

  .wordmark {
    font-family: "Montserrat", Arial, sans-serif;
    font-weight: 500;
    color: var(--teal);
    letter-spacing: 4px;
    position: absolute;
    white-space: nowrap;
  }
  .card--front .wordmark {
    font-size: 62px;
    left: 50%;
    top: 50%;
    transform: translate(-50%, -50%);
  }
  .card--back .wordmark {
    font-size: 52px;
    right: 44px;
    top: 132px;
  }

  .accent-tab {
    position: absolute;
    left: -22px;
    top: 30px;
    width: 44px;
    height: 44px;
    border-radius: 50%;
    background: var(--teal);
  }
  .identity { position: absolute; left: 44px; top: 30px; }
  .identity__name {
    color: var(--ink);
    font-weight: 600;
    font-size: 22px;
    line-height: 1.2;
  }
  .identity__title {
    color: var(--ink-soft);
    font-size: 12px;
    margin-top: 2px;
  }

  .contacts {
    position: absolute;
    left: 30px;
    bottom: 46px;
    list-style: none;
  }
  .contacts__item {
    display: flex;
    align-items: center;
    gap: 10px;
    color: var(--ink);
    font-size: 15px;
    line-height: 24px;
  }
  .contacts__icon {
    width: 16px;
    height: 16px;
    border-radius: 50%;
    background: var(--ink);
    display: flex;
    align-items: center;
    justify-content: center;
    flex: none;
  }
  .contacts__icon svg { width: 10px; height: 10px; }
</style>
</head>
<body>
  <section class="card card--front">
    <div class="wordmark">ZELQUIN</div>
  </section>

  <section class="card card--back">
    <span class="accent-tab"></span>
    <div class="identity">
      <p class="identity__name">Dana Reyes Hart</p>
      <p class="identity__title">Managing Director</p>
    </div>
    <div class="wordmark">ZELQUIN</div>
    <ul class="contacts">
      <li class="contacts__item">
        <span class="contacts__icon">
          <svg viewBox="0 0 10 10"><path d="M2 1h2l1 2-1 1c.6 1.2 1.4 2 2.6 2.6l1-1 2 1v2c0 .6-.4 1-1 1C4.5 9.6.4 5.5 1 2c0-.6.4-1 1-1z" fill="#1f2021"/></svg>
        </span>555.014.2837
      </li>
      <li class="contacts__item">
        <span class="contacts__icon">
          <svg viewBox="0 0 10 10"><rect x="1" y="2.5" width="8" height="5" rx=".6" fill="#1f2021"/><path d="M1.3 2.8 5 5.6l3.7-2.8" stroke="#f2f2f2" stroke-width=".7" fill="none"/></svg>
        </span>danahart@zelquin.com
      </li>
      <li class="contacts__item">
        <span class="contacts__icon">
          <svg viewBox="0 0 10 10"><circle cx="5" cy="5" r="3.8" fill="none" stroke="#1f2021" stroke-width=".9"/><path d="M1.2 5h7.6M5 1.2c-2 2.3-2 5.3 0 7.6M5 1.2c2 2.3 2 5.3 0 7.6" stroke="#1f2021" stroke-width=".7" fill="none"/></svg>
        </span>www.zelquin.com
      </li>
    </ul>
  </section>
</body>
</html>
```